Simple and Clean business card design

We would like the design to be simple clean and to incorporate our colors.

We are open to your design and talent, we have the dots in our logo as we think of it as data points and we connect data points for people.

We are open to see the great creative and clean design you bring to the table

Contact Information for Business Card

please include: name, position, email, phone and website

Font styles to use
Sans Serif

Requirements
Must have
• my colors incorporated, simplicity
Nice to have
• lots of white space, simplicity
Should not have
• complexicity/ complex art

```html
<!DOCTYPE html>
<html lang="en">
<head>
<meta charset="utf-8">
<title>Dotwise business card</title>
<link rel="stylesheet" href="https://fonts.googleapis.com/css2?family=Montserrat:wght@600&family=Lato:wght@700&family=Roboto:wght@400&display=swap">
<style>
  :root {
    --backdrop: #e3e3e3;
    --ink: #111111;
    --paper: #ffffff;
    --blue: #4285f4;
    --green: #34a853;
    --yellow: #fbbc05;
    --red: #ea4335;
    --orange: #f97a1f;
  }
  html, body {
    margin: 0;
    padding: 0;
    width: 1200px;
    height: 900px;
    overflow: hidden;
    background: var(--backdrop);
  }
  .canvas {
    position: relative;
    width: 1200px;
    height: 900px;
  }
  .card {
    position: absolute;
    top: 216px;
    width: 309px;
    height: 501px;
    box-shadow: 2px 3px 6px rgba(0,0,0,0.25);
    overflow: hidden;
  }
  .card-front {
    left: 279px;
    border-radius: 0 60px 0 60px;
    background: linear-gradient(135deg,
      var(--yellow) 0%,
      var(--orange) 22%,
      var(--red) 38%,
      var(--orange) 48%,
      var(--yellow) 58%,
      var(--green) 74%,
      var(--blue) 100%);
    background:
      linear-gradient(225deg, var(--red) 0%, var(--red) 18%, var(--orange) 30%, var(--yellow) 42%, rgba(251,188,5,0) 56%),
      linear-gradient(45deg, var(--blue) 0%, #3a92c4 18%, var(--green) 38%, #8cc02a 55%, var(--yellow) 75%, var(--orange) 100%);
  }
  .front-wordmark {
    position: absolute;
    left: 0;
    right: 0;
    top: 370px;
    text-align: center;
    font-family: "Montserrat", sans-serif;
    font-weight: 600;
    font-size: 54px;
    letter-spacing: 0.5px;
    color: var(--paper);
  }
  .card-back {
    left: 617px;
    background: var(--paper);
    border-radius: 60px 0 60px 0;
  }
  .back-logo {
    position: absolute;
    left: 44px;
    top: 112px;
    display: flex;
    align-items: center;
    gap: 8px;
  }
  .back-logo .dot {
    width: 16px;
    height: 16px;
    border-radius: 50%;
    background: var(--blue);
  }
  .back-wordmark {
    font-family: "Montserrat", sans-serif;
    font-weight: 600;
    font-size: 50px;
    color: var(--ink);
    line-height: 1;
  }
  .person {
    position: absolute;
    left: 36px;
    top: 328px;
  }
  .person-name {
    margin: 0;
    font-family: "Lato", sans-serif;
    font-weight: 700;
    font-size: 22px;
    color: var(--ink);
    line-height: 1.1;
  }
  .person-role {
    margin: 2px 0 0;
    font-family: "Roboto", sans-serif;
    font-size: 14.5px;
    color: var(--blue);
  }
  .contacts {
    position: absolute;
    left: 36px;
    top: 398px;
    margin: 0;
    padding: 0;
    list-style: none;
    font-family: "Roboto", sans-serif;
    font-size: 14.5px;
    color: var(--ink);
  }
  .contacts li {
    display: flex;
    align-items: center;
    gap: 6px;
    height: 21px;
  }
  .contacts svg { width: 16px; height: 16px; flex: none; }
  .contacts .highlight { color: var(--blue); }
</style>
</head>
<body>
<div class="canvas">
  <div class="card card-front">
    <div class="front-wordmark">Dotwise</div>
  </div>

  <div class="card card-back">
    <div class="back-logo">
      <span class="back-wordmark">Dotwise</span>
      <span class="dot"></span>
    </div>

    <div class="person">
      <p class="person-name">Marcus Lane</p>
      <p class="person-role">Founder/ CEO</p>
    </div>

    <ul class="contacts">
      <li>
        <svg viewBox="0 0 16 16" aria-hidden="true">
          <circle cx="8" cy="8" r="8" fill="var(--green)"/>
          <path d="M5.3 4.2l1.3-.2.8 1.9-.9.7c.4.9 1.1 1.6 2 2l.7-.9 1.9.8-.2 1.3c-.1.5-.5.8-1 .8C7 10.5 4.6 8.1 4.5 5.2c0-.5.3-.9.8-1z" fill="#fff"/>
        </svg>
        <span>555-214-0387</span>
      </li>
      <li>
        <svg viewBox="0 0 16 16" aria-hidden="true">
          <circle cx="8" cy="8" r="8" fill="var(--yellow)"/>
          <rect x="4" y="5.2" width="8" height="5.6" rx="0.6" fill="#fff"/>
          <path d="M4.3 5.6L8 8.4l3.7-2.8" fill="none" stroke="var(--yellow)" stroke-width="0.9"/>
        </svg>
        <span>marcus.lane@dotwise.one</span>
      </li>
      <li>
        <svg viewBox="0 0 16 16" aria-hidden="true">
          <circle cx="8" cy="8" r="8" fill="var(--red)"/>
          <g fill="none" stroke="#fff" stroke-width="0.9">
            <circle cx="8" cy="8" r="4"/>
            <ellipse cx="8" cy="8" rx="1.8" ry="4"/>
            <path d="M4 8h8M4.6 6h6.8M4.6 10h6.8"/>
          </g>
        </svg>
        <span>www.<span class="highlight">Dotwise</span>.one</span>
      </li>
    </ul>
  </div>
</div>
</body>
</html>
```